Quimbly Needs a 1 Page Redesign with UI/UX Elements

Quimbly is a GIF creation and sharing site. We are upgrading one of our main responsive website pages. [Please see: http://quimblyzone.net/R-4TzLa for an example]

Need design versions for Desktop, tablet & mobile.

Also need frontend development to implement page. Currently on Foundation framework.

There are many functions/nav elements that need to be on this page in an uncluttered and clear manner. Not all of functions need to be shown at all times. Need a designer with UI/UX background to incorporate these and make it easy to navigate for the user.

The designer needs to be familiar with the site to understand each function. Color scheme will remain the same as current site.

If there are Dropdowns/collapsed or hidden features - need to know how they look when opened.

Target Market(s)

Quimbly has a varied demographic but focuses on under 25.

Coding

Coded - Design and coding required

Number of Pages Required

1 page

Font styles to use
Sans Serif

Requirements
Must have
• The top and bottom nav bars must stay the same. We are not redesigning the whole site yet, just that page.
• This page is developed with sharing in mind. Our top 3 actions are highlighted below. Be creative & think about user experience as our #1 priority
• Desktop
•  SOCIAL SHARE BUTTONS Zentrova/Plinkit/Voxmora/Brolendar
•  Download Button
•  Create a GIF Button
• OTHER FEATURES THAT MUST BE INCLUDED
• Share This With Friends pop up
• Title of GIF
• Added XX days ago by XXXX in XXX
• Source
• Thumbs up votes showing numerically (no down vote thumb)
• Total Views
• Embed Links: direct, website, message board, markdown
• NSFW Flag
• MP4 to GIF toggle
• Next arrows to scroll through GIFs
• Scroll thumbnail bar for like GIFs at the bottom of the page
• NEW FEATURES TO IMPLEMENT
• Favorite (bookmark Option)
• LOGGED IN USERS:
• Logged in users also have Private Button & Delete Button
• MOBILE
• We would like to keep the mobile page as minimalist as possible.
• Download button
• Create a GIF button
• Sharing button: Drovanel, Zentrova, Plinkit, Voxmora,
• Share Via SMS
• (Please incorporate the share buttons in a creative & clean way)
• Three dots that would open up to reveal tags
• Thumbnail scroll at bottom for GIFs in the same category
Nice to have
• Be creative with how the page features are laid out. We want it to be easy for users to navigate & clear what actions are there.
Should not have
• Basically anything that is on the page now. The buttons don't look like buttons & there is no drive to any actions (like sharing). Please see attached file for what NOT to do.

```html
<!DOCTYPE html>
<html lang="en">
<head>
<meta charset="utf-8">
<title>Quimbly – GIF page</title>
<link href="https://fonts.googleapis.com/css2?family=Open+Sans:wght@400;600;700&display=swap" rel="stylesheet">
<style>
:root{
  --yellow:#f7bd16;
  --header:#454545;
  --footer:#3a3a3a;
  --footer-deep:#2e2e2e;
  --btn-dark:#3b3b3b;
  --page:#f3f3f3;
  --card:#ffffff;
  --panel:#ececec;
  --text:#333333;
  --muted:#777777;
  --zentrova:#3b5998;
  --plinkit:#29a9e1;
  --voxmora:#c4161c;
  --drovanel:#5b3a2e;
}
*{box-sizing:border-box;margin:0;padding:0}
html,body{width:1050px;height:1200px;overflow:hidden}
body{background:var(--page);font-family:"Open Sans",sans-serif;color:var(--text);position:relative}

/* header */
.site-header{position:absolute;left:0;top:0;width:1050px;height:60px;background:var(--header)}
.brand{position:absolute;left:86px;top:17px;display:flex;align-items:center;gap:8px;color:#fff;font-weight:700;font-size:22px;line-height:26px}
.brand-mark{width:26px;height:26px;background:var(--yellow);border-radius:4px}
.search-icon{position:absolute;left:774px;top:23px}
.login-btn{position:absolute;top:18px;height:26px;font-size:12px;color:#fff;display:flex;align-items:center;justify-content:center;gap:6px;border-radius:2px}
.login-btn.dark{left:804px;width:78px;background:#2f2f2f}
.login-btn.gold{left:886px;width:77px;background:var(--yellow);color:#2f2f2f}

/* nav */
.main-nav{position:absolute;left:0;top:60px;width:1050px;height:40px;background:var(--yellow)}
.main-nav a{position:absolute;top:0;height:40px;line-height:40px;font-size:12.5px;font-weight:600;color:#3a3a3a;text-decoration:none;white-space:nowrap}
.main-nav a.active{background:var(--btn-dark);color:#fff;padding:0 17px;left:86px}

/* card */
.gif-card{position:absolute;left:86px;top:120px;width:877px;height:702px;background:var(--card)}
.gif-stage{position:absolute;left:0;top:0;width:877px;height:417px;background:linear-gradient(100deg,#c9c3bb 0%,#b8866d 35%,#a8654b 60%,#8b4a38 100%)}
.stage-arrow{position:absolute;top:188px;width:35px;height:49px;background:rgba(60,60,60,.75);display:flex;align-items:center;justify-content:center}
.share-pop{position:absolute;left:640px;top:370px;width:189px;height:47px;background:rgba(55,55,55,.92);border-radius:2px;color:#fff}
.share-pop h4{font-weight:400;font-size:12.5px;position:absolute;left:22px;top:5px;white-space:nowrap}
.share-pop .close{position:absolute;right:8px;top:3px;font-size:11px}
.share-pop .dots{position:absolute;left:24px;top:27px;display:flex;gap:7px}
.share-pop .dots span{width:14px;height:14px;display:block}
.share-pop::after{content:"";position:absolute;left:12px;bottom:-8px;border:8px solid transparent;border-top-color:rgba(55,55,55,.92);border-bottom:0}

.gif-title{position:absolute;left:32px;top:437px;font-size:24px;font-weight:400;color:#333;white-space:nowrap}
.gif-meta{position:absolute;left:30px;top:471px;font-size:13px;color:var(--muted);white-space:nowrap}
.format-toggle{position:absolute;left:709px;top:447px;width:145px;height:34px;border-radius:17px;background:#f1f1f1;border:1px solid #e2e2e2}
.format-toggle span{position:absolute;top:0;height:32px;line-height:32px;font-size:14px}
.format-toggle .mp4{left:12px;color:#555}
.format-toggle .gif{right:0;width:64px;text-align:center;background:var(--yellow);border-radius:16px;color:#fff}

.source-panel{position:absolute;left:30px;top:512px;width:817px;height:87px;background:var(--panel);border-radius:2px}
.source-label{position:absolute;left:27px;top:33px;font-size:13.5px;color:#555;white-space:nowrap}
.source-label b{font-weight:400;margin-right:9px}
.create-from-video{position:absolute;left:303px;top:30px;width:188px;height:30px;background:var(--btn-dark);color:#fff;font-size:12px;line-height:30px;text-align:center;border-radius:2px;white-space:nowrap}
.votes{position:absolute;left:746px;top:33px;font-size:12px;color:#555;display:flex;align-items:center;gap:5px}

.action-row{position:absolute;left:30px;top:627px;display:flex;gap:7px}
.action-btn{width:110px;height:28px;background:var(--btn-dark);color:#fff;font-size:11px;display:flex;align-items:center;justify-content:center;gap:6px;border-radius:2px;white-space:nowrap}
.action-btn.primary{background:var(--yellow);color:#3a3a3a}
.nsfw{position:absolute;left:816px;top:680px;font-size:10px;letter-spacing:1.5px;color:#555;font-family:"Courier New",monospace}

/* side share */
.side-share{position:absolute;left:0;width:75px;height:28px;color:#fff;font-size:12px;font-weight:600;display:flex;align-items:center;gap:10px;padding-left:8px;border-radius:0 2px 2px 0}
.side-share i{width:10px;height:10px;background:rgba(255,255,255,.85);display:block}

/* related */
.related-title{position:absolute;left:84px;top:868px;font-size:24px;font-weight:400;color:#333}
.carousel-nav{position:absolute;top:879px;width:18px;height:18px;border-radius:50%;display:flex;align-items:center;justify-content:center}
.thumb{position:absolute;top:917px;width:162px;height:121px}

/* footer */
.site-footer{position:absolute;left:0;top:1125px;width:1050px;height:75px;background:var(--footer)}
.footer-links{position:absolute;left:0;top:0;width:1050px;height:40px;line-height:40px;text-align:center;font-size:11px;color:#fff}
.footer-links span.sep{margin:0 8px}
.footer-tag{position:absolute;right:38px;top:12px;font-size:11px;color:#fff}
.footer-base{position:absolute;left:0;top:40px;width:1050px;height:35px;background:var(--footer-deep)}
.copyright{position:absolute;left:84px;top:11px;font-size:10.5px;color:#fff}
.footer-social{position:absolute;left:899px;top:7px;display:flex;gap:2px}
.footer-social span{width:20px;height:20px;display:block}
</style>
</head>
<body>

<header class="site-header">
  <div class="brand"><span class="brand-mark"></span>Quimbly</div>
  <svg class="search-icon" width="16" height="16" viewBox="0 0 16 16"><circle cx="6.5" cy="6.5" r="5" fill="none" stroke="#fff" stroke-width="2"/><line x1="10" y1="10" x2="14.5" y2="14.5" stroke="#fff" stroke-width="2"/></svg>
  <div class="login-btn dark"><svg width="10" height="10" viewBox="0 0 10 10"><circle cx="3" cy="3" r="2.5" fill="#fff"/><line x1="4" y1="4" x2="9" y2="9" stroke="#fff" stroke-width="1.6"/></svg>Login</div>
  <div class="login-btn gold"><svg width="9" height="10" viewBox="0 0 9 10"><circle cx="4.5" cy="3" r="2.5" fill="#2f2f2f"/><path d="M0 10a4.5 4 0 0 1 9 0z" fill="#2f2f2f"/></svg>Login</div>
</header>

<nav class="main-nav">
  <a class="active">The Gallery</a>
  <a style="left:213px">Pictures to Gif</a>
  <a style="left:336px">Vidlume to Gif</a>
  <a style="left:463px">Upload a Gif</a>
  <a style="left:577px">Video to Gif</a>
  <a style="left:687px">Webcam to Gif</a>
</nav>

<main class="gif-card">
  <div class="gif-stage" role="img" aria-label="Animated GIF: a smiling couple in hats and sunglasses riding bicycles down a brick street"></div>
  <div class="stage-arrow" style="left:0"><svg width="8" height="12" viewBox="0 0 8 12"><path d="M6 1 1 6l5 5" fill="none" stroke="#fff" stroke-width="1.6"/></svg></div>
  <div class="stage-arrow" style="right:0"><svg width="8" height="12" viewBox="0 0 8 12"><path d="M2 1l5 5-5 5" fill="none" stroke="#fff" stroke-width="1.6"/></svg></div>

  <div class="share-pop">
    <h4>Share this with Friends</h4>
    <span class="close">✖</span>
    <div class="dots"><span style="background:var(--zentrova)"></span><span style="background:var(--drovanel)"></span><span style="background:var(--plinkit)"></span></div>
  </div>

  <h1 class="gif-title">Chatterlo fullscreen responsiv</h1>
  <p class="gif-meta">Added 7 days ago by pixelharbor in funny gifs</p>

  <div class="format-toggle"><span class="mp4">MP4</span><span class="gif">GIF</span></div>

  <section class="source-panel">
    <p class="source-label"><b>SOURCE:</b> Watch the full Vidlume video</p>
    <div class="create-from-video">Create Gif From This Video</div>
    <div class="votes"><svg width="18" height="18" viewBox="0 0 18 18"><path d="M2 8h3v8H2zM5 8l4-6c1.5 0 2 1 1.6 2.5L10 7h5a1.5 1.5 0 0 1 1.4 1.9l-1.8 6A1.5 1.5 0 0 1 13 16H5z" fill="none" stroke="#444" stroke-width="1.3" stroke-linejoin="round"/></svg>(347)</div>
  </section>

  <div class="action-row">
    <div class="action-btn primary"><svg width="11" height="9" viewBox="0 0 11 9"><path d="M3 8.5h5.5a2.5 2.5 0 0 0 0-5A3.5 3.5 0 0 0 1.6 4 2.3 2.3 0 0 0 3 8.5z" fill="#3a3a3a"/></svg>Download</div>
    <div class="action-btn"><svg width="9" height="9" viewBox="0 0 9 9"><path d="M4.5 0v9M0 4.5h9" stroke="#fff" stroke-width="2"/></svg>More</div>
    <div class="action-btn"><svg width="11" height="9" viewBox="0 0 11 9"><path d="M1 5l3 3 6-7" fill="none" stroke="#fff" stroke-width="2"/></svg>Create Gif</div>
    <div class="action-btn"><svg width="12" height="8" viewBox="0 0 12 8"><path d="M0 4q6-7 12 0-6 7-12 0z" fill="#fff"/><circle cx="6" cy="4" r="1.6" fill="#3b3b3b"/></svg>15 total views</div>
    <div class="action-btn"><svg width="11" height="11" viewBox="0 0 11 11"><path d="M4.5 6.5 6.5 4.5M3 6 1.5 7.5a1.8 1.8 0 0 0 2.5 2.5L5.5 8.5M8 5l1.5-1.5A1.8 1.8 0 0 0 7 1L5.5 2.5" fill="none" stroke="#fff" stroke-width="1.4"/></svg>Embedded Links</div>
    <div class="action-btn"><svg width="11" height="9" viewBox="0 0 11 9"><path d="M1 6 10 1 7 8 5 6z" fill="#fff"/></svg>GIF to Plinkit</div>
    <div class="action-btn"><svg width="11" height="11" viewBox="0 0 11 11"><path d="M5.5 0l1.6 3.5 3.9.4-2.9 2.6.8 3.8-3.4-2-3.4 2 .8-3.8L0 3.9l3.9-.4z" fill="#fff"/></svg>Favorite</div>
  </div>
  <span class="nsfw">NSFW</span>
</main>

<div class="side-share" style="top:570px;background:var(--zentrova)"><i></i>Share</div>
<div class="side-share" style="top:603px;background:var(--plinkit)"><i></i>Share</div>
<div class="side-share" style="top:636px;background:var(--voxmora)"><i></i>Share</div>
<div class="side-share" style="top:670px;background:var(--drovanel)"><i></i>Share</div>

<h2 class="related-title">Check out these funny gifs</h2>
<div class="carousel-nav" style="left:924px;background:var(--yellow)"><svg width="6" height="9" viewBox="0 0 6 9"><path d="M5 1 1.5 4.5 5 8" fill="none" stroke="#333" stroke-width="1.6"/></svg></div>
<div class="carousel-nav" style="left:945px;background:#2f2f2f"><svg width="6" height="9" viewBox="0 0 6 9"><path d="M1 1l3.5 3.5L1 8" fill="none" stroke="#fff" stroke-width="1.6"/></svg></div>

<div class="thumb" style="left:86px;background:linear-gradient(135deg,#3f6b4a,#2c4f36)" role="img" aria-label="GIF thumbnail: man in glasses posing in front of a chalkboard"></div>
<div class="thumb" style="left:266px;background:linear-gradient(135deg,#4fb0d6,#2a5f9e)" role="img" aria-label="GIF thumbnail: friends posing with party props"></div>
<div class="thumb" style="left:444px;background:linear-gradient(135deg,#a9c2cf,#4f7792)" role="img" aria-label="GIF thumbnail: two people on a couch holding funny masks"></div>
<div class="thumb" style="left:622px;background:linear-gradient(135deg,#2f4560,#182538)" role="img" aria-label="GIF thumbnail: two men flexing muscles"></div>
<div class="thumb" style="left:801px;background:linear-gradient(135deg,#6b6b6b,#3c3c3c)" role="img" aria-label="GIF thumbnail: excited man giving thumbs up"></div>

<footer class="site-footer">
  <div class="footer-links">Upload a Gif<span class="sep">|</span>Video to Gif<span class="sep">|</span>Webcam to Gif<span class="sep">|</span>Vidlume to Gif<span class="sep">|</span>Privacy Policy<span class="sep">|</span>Contact Us<span class="sep">|</span>Request Deletion</div>
  <span class="footer-tag">M3</span>
  <div class="footer-base">
    <p class="copyright">© 2015 Yoursite, All rights reserved.</p>
    <div class="footer-social"><span style="background:var(--zentrova)"></span><span style="background:var(--drovanel)"></span><span style="background:var(--plinkit)"></span></div>
  </div>
</footer>

</body>
</html>
```